Upscale business cards needed for Board of Directors

We need professional business cards created for members of our family business Board of Directors. We would like these relatively simple and straightforward, but also with a unique element to set them apart. Probably stick with neutral and simple colors - white, grey etc. We need space for the traditional elements, including name, title, address, email/phone number. And we will be creating several from this template so it needs to be template that is easy to switch information in and out of.
Business
See description

```html
<!DOCTYPE html>
<html lang="en">
<head>
<meta charset="utf-8">
<title>Harborline Holdings – Business Card</title>
<link href="https://fonts.googleapis.com/css2?family=Open+Sans:wght@600;700&family=Marcellus+SC&family=Courier+Prime&display=swap" rel="stylesheet">
<style>
  :root {
    --backdrop: #e9e7e3;
    --card: #ffffff;
    --ink: #1f1c1d;
    --ink-soft: #3b3636;
    --muted: #7d746c;
    --accent: #b09c80;
    --divider: #e4e1dd;
  }
  * { margin: 0; padding: 0; box-sizing: border-box; }
  html, body {
    width: 1200px; height: 799px; overflow: hidden;
    background: var(--backdrop);
  }
  .business-card {
    position: absolute;
    left: 180px; top: 160px;
    width: 840px; height: 480px;
    background: linear-gradient(160deg, #ffffff 0%, #fbfaf9 60%, #f4f2ef 100%);
    box-shadow: 0 10px 30px rgba(0,0,0,0.12);
    font-family: "Open Sans", Arial, sans-serif;
    color: var(--ink-soft);
  }
  .company-name {
    position: absolute;
    left: 0; right: 0; top: 70px;
    padding-left: 140px;
    text-align: center;
    font-family: "Open Sans", Arial, sans-serif;
    font-weight: 700;
    font-size: 46px;
    letter-spacing: 2px;
    line-height: 1.1;
    text-transform: uppercase;
    color: var(--ink);
  }
  .person {
    position: absolute;
    left: 52px; top: 200px;
  }
  .person-name {
    font-family: "Marcellus SC", Georgia, serif;
    font-size: 32px;
    color: var(--ink);
    letter-spacing: 0.5px;
  }
  .person-title {
    font-family: "Courier Prime", "Courier New", monospace;
    font-size: 19px;
    color: var(--muted);
    letter-spacing: 1.5px;
    margin-top: 2px;
  }
  .column-divider {
    position: absolute;
    left: 336px; top: 190px;
    width: 2px; height: 260px;
    background: linear-gradient(180deg, transparent, var(--divider) 20%, var(--divider) 80%, transparent);
  }
  .contact-list {
    position: absolute;
    left: 380px; top: 205px;
    list-style: none;
  }
  .contact-item {
    display: flex;
    align-items: flex-start;
    margin-bottom: 28px;
    font-weight: 600;
    font-size: 16px;
    line-height: 1.35;
    text-transform: uppercase;
    letter-spacing: 0.3px;
  }
  .contact-icon {
    width: 26px; height: 22px;
    flex: none;
    margin-right: 30px;
    fill: var(--accent);
  }
</style>
</head>
<body>
  <main class="business-card">
    <div class="company-name">Harborline Holdings</div>

    <section class="person">
      <div class="person-name">Name Surname</div>
      <div class="person-title">Designation</div>
    </section>

    <div class="column-divider"></div>

    <ul class="contact-list">
      <li class="contact-item">
        <svg class="contact-icon" viewBox="0 0 26 22" aria-hidden="true">
          <path d="M2 4h22v14H2z" fill="none" stroke="#b09c80" stroke-width="2"/>
          <path d="M2 4l11 8 11-8" fill="none" stroke="#b09c80" stroke-width="2"/>
        </svg>
        <span>info@companyname.com</span>
      </li>
      <li class="contact-item">
        <svg class="contact-icon" viewBox="0 0 26 22" aria-hidden="true">
          <path d="M6 2c1.5 0 2.5 3 2.5 4.5S6.5 8 7 10s3 5 5 6 2.5-1.5 4-1.5 4 1.5 4 3-2 3-4 3C10 20 4 13 3.5 7 3.3 4 4.5 2 6 2z"/>
        </svg>
        <span>+1 555 0142 7789<br>+1 555 0198 7684</span>
      </li>
      <li class="contact-item">
        <svg class="contact-icon" viewBox="0 0 26 22" aria-hidden="true">
          <path d="M13 2L2 11h3v9h6v-6h4v6h6v-9h3z"/>
        </svg>
        <span>Your City Address<br>Street Location, NY City, USA</span>
      </li>
      <li class="contact-item">
        <svg class="contact-icon" viewBox="0 0 26 22" aria-hidden="true">
          <circle cx="13" cy="11" r="10"/>
          <g fill="none" stroke="#ffffff" stroke-width="1.2">
            <circle cx="13" cy="11" r="6.5"/>
            <ellipse cx="13" cy="11" rx="3" ry="6.5"/>
            <path d="M6.5 11h13M7.5 7.5h11M7.5 14.5h11"/>
          </g>
        </svg>
        <span>www.company-name.com</span>
      </li>
    </ul>
  </main>
</body>
</html>
```